Summit Ridge Business Card

Side 1: Summit Ridge Logo (logo without Maltese cross) with industrial rope rescue related theme. Our company services - TRAINING - Fire Training, Confined Space Rescue Training, Rope Rescue training, Hazmat Training, Incident Command, EMS, Pump Operations Training. Website - summitridgeexample.com.
Side 2: Summit Ridge Fire Department Logo (logo with Maltese cross) with Firefighter related theme. Company (division) services - FIELD SERVICES - Fire Department, Stand-by Rescue, Safety, EMS, Planning. "Supporting the Emergency Response Community Since 1967"

Add contact information wherever it makes since (Name, Email, Phone).
I would like it to represent the Summit Ridge Fire Department Logo as a division not as a separate entity without saying it, possibly by depicting it in the background of Side 2 instead of being a standalone picture like the logo on Side 1.

```html
<!DOCTYPE html>
<html lang="en">
<head>
<meta charset="utf-8">
<title>Summit Ridge Business Card</title>
<link href="https://fonts.googleapis.com/css2?family=Poppins:ital,wght@0,400;0,500;0,600;0,700;1,400&display=swap" rel="stylesheet">
<style>
  :root {
    --page: #2a2a2a;
    --card: #ffffff;
    --red: #e8432a;
    --red-bright: #e8262a;
    --ink: #111111;
    --text: #222222;
  }
  * { margin: 0; padding: 0; box-sizing: border-box; }
  html, body { width: 1093px; height: 1200px; overflow: hidden; }
  body {
    background: var(--page);
    font-family: "Poppins", sans-serif;
    color: var(--text);
    position: relative;
  }
  .card {
    position: absolute;
    background: var(--card);
    border-radius: 30px;
    box-shadow: 2px 4px 6px rgba(0,0,0,0.45);
  }
  .card--field { left: 265px; top: 226px; width: 576px; height: 356px; }
  .card--training { left: 265px; top: 621px; width: 581px; height: 356px; }

  .section-title {
    position: absolute;
    font-weight: 600;
    font-size: 21px;
    color: var(--red);
    letter-spacing: 0.2px;
    line-height: 1;
  }
  .card--field .section-title { left: 26px; top: 36px; }
  .card--training .section-title { left: 20px; top: 45px; color: var(--red-bright); }

  .service-list {
    position: absolute;
    list-style: none;
    font-size: 17.5px;
    line-height: 21px;
    color: var(--text);
  }
  .service-list li { position: relative; padding-left: 12px; white-space: nowrap; }
  .service-list li::before {
    content: "";
    position: absolute;
    left: 0; top: 7px;
    width: 7px; height: 7px;
    border-radius: 50%;
    background: var(--red);
  }
  .card--field .service-list { left: 26px; top: 74px; }
  .card--training .service-list { left: 22px; top: 89px; }
  .card--training .service-list li { padding-left: 18px; }
  .card--training .service-list li::before { left: 2px; background: var(--red-bright); }

  .contact-name {
    position: absolute;
    left: 26px; top: 206px;
    font-weight: 600;
    font-size: 22px;
    color: var(--ink);
    line-height: 1.2;
  }
  .contact-details {
    position: absolute;
    left: 26px; top: 246px;
    font-size: 17.5px;
    line-height: 21px;
    color: var(--text);
    list-style: none;
  }
  .contact-details li { display: flex; align-items: center; gap: 6px; white-space: nowrap; }
  .contact-details svg { width: 16px; height: 16px; flex: none; }

  .tagline {
    position: absolute;
    left: 25px; top: 305px;
    font-style: italic;
    font-size: 15.5px;
    color: var(--red);
    white-space: nowrap;
  }

  .brand {
    position: absolute;
    display: flex;
    align-items: center;
    justify-content: center;
    gap: 10px;
    font-weight: 600;
    white-space: nowrap;
  }
  .brand__dot { width: 14px; height: 14px; border-radius: 50%; flex: none; }
  .card--field .brand { left: 333px; top: 51px; width: 216px; height: 217px; font-size: 24px; color: var(--red); }
  .card--field .brand__dot { background: var(--red); }
  .card--training .brand { left: 314px; top: 85px; width: 236px; height: 153px; font-size: 30px; color: var(--red-bright); }
  .card--training .brand__dot { background: var(--red-bright); }

  .website {
    position: absolute;
    left: 22px; top: 274px;
    font-size: 18px;
    color: var(--text);
  }
  .website .accent { color: var(--red-bright); }
</style>
</head>
<body>

  <section class="card card--field" aria-label="Field services side">
    <h2 class="section-title">FIELD SERVICES</h2>
    <ul class="service-list">
      <li>Fire Department</li>
      <li>Stand-by Rescue</li>
      <li>Safety</li>
      <li>EMS</li>
      <li>Planning</li>
    </ul>
    <p class="contact-name">Daniel Hartley</p>
    <ul class="contact-details">
      <li>
        <svg viewBox="0 0 16 16" aria-hidden="true"><path d="M3.5 1.5l2.5 2.7-1.2 1.9c.9 2 2.4 3.5 4.3 4.4l1.9-1.2 2.7 2.5-1.4 2.2C7.5 13.7 2.3 8.5 1.3 2.9z" fill="none" stroke="#e8432a" stroke-width="1.5" stroke-linejoin="round"/><path d="M9.5 2.5a4 4 0 0 1 4 4M9.5 0.8a5.7 5.7 0 0 1 5.7 5.7" fill="none" stroke="#e8432a" stroke-width="1.2"/></svg>
        044-555 010 247
      </li>
      <li>
        <svg viewBox="0 0 16 16" aria-hidden="true"><rect x="0.5" y="3" width="15" height="10" fill="#e8432a"/><path d="M0.5 3l7.5 6 7.5-6M0.5 13l5.5-5M15.5 13l-5.5-5" fill="none" stroke="#fff" stroke-width="1"/></svg>
        info@summitridgeexample.com
      </li>
    </ul>
    <p class="tagline">Supporting the Emergency Response Community Since 1967</p>
    <div class="brand"><span class="brand__dot"></span>Summit Ridge</div>
  </section>

  <section class="card card--training" aria-label="Training side">
    <h2 class="section-title">TRAINING</h2>
    <ul class="service-list">
      <li>Fire Training</li>
      <li>Confined Space Rescue Training</li>
      <li>Rope Rescue training</li>
      <li>Hazmat Training</li>
      <li>Incident Command</li>
      <li>EMS</li>
      <li>Pump Operations Training</li>
    </ul>
    <div class="brand"><span class="brand__dot"></span>Summit Ridge</div>
    <p class="website">www.<span class="accent">summitridgeexample</span>.com</p>
  </section>

</body>
</html>
```